REdesign Landing Page für Reise- und Touristikportal
Zielgruppe
Nachtrag 25.10.21: es bedarf keines neuen Logos. Aber die Angebotsboxen auf der Startseite, die auch in den Reiserubriken vorzufinden sind, dürfen gern optisch angepasst werden. Die jeweilige Balkenfarbe ist stets die Farbe des Reiseveranstalters und das Logo des Veranstalters in der Box sollte weiterhin vorhanden sein (dienen zur Wiedererkennung).
Reise- und Touristikportal https://wegfinderei.de, mit zahlreichen Reiseangeboten namhafter (Spezial-) Reiseveranstalter. Es handelt sich um ein Affiliate Portal, d.h. die Reisen werden stets auf der Seite der Reiseveranstalter gebucht. Zielgruppe, sind die Personen, die Wert auf schöne Reisen legen (kein Mainstream wie VAK), die ihre Reisen auch z.b. nach ihrem Hobby aussuchen wollen (z.B. Motorradreisen, Tauchreisen etc.) oder auch besondere Filterfunktionen zum Finden der Reise nutzen möchten.
Aufgabenstellung
- Redesign Startseite mit 'Hier will ich bleiben' Effekt (nicht nur Farbänderung oder Elemente anders platzieren)
- wirkungsvolles responsive Design soll unsere Zielgruppe neugierig machen, ansprechen und zum Anklicken der Angebote, Verweilen einladen
- angenehmes Farbschemata (above/under the fold)
- ansprechende Aufteilung der Startseiten Bereiche (aktuell wirkt das alles wie ein 'Schlauch')
- mobil leicht zu bedienen (das ist aktuell ein großes Problem, wegen der 53 Reisethemen Kacheln)
- wir möchten mit der neuen Startseite das Bedürfnis nach Urlaub wecken und auf Reiseveranstalter Seite das Gefühl wecken 'Hier müssen wir unbedingt unsere Angebote einstellen'
- ein schöner Footer (der jetzige ist fürchterlich)
- schlanke Performance (IT Umsetzung erfolgt dann durch einen Programmierer)
- die engl. Seite fällt künftig weg, also Entwurf ohne den 'de' Umschalter
Ich bin nicht an das jetzige Design, Schriften der Startseite, Anordnung der einzelnen Bereiche gebunden. Allerdings wird an den Reiserubrikseiten designmäßig nichts bis wenig geändert werden (außer es ginge schnell) und die Startseite soll natürlich weiterhin zum Rest der Webseite passen. Aktuell verwendete Schriftart: Lato.
Man kann auch z.B. Neues integrieren wie z.B. 'Was für ein Reisetyp bist Du?' oder 'Was ist Deine Lieblingsreisezeit?' als eine Art Quiz (technisch würde das von einem Programmierer umgesetzt werden)
Ich kann auch Zugang zu Lumora Bildarchiv geben. Man könnte z.b. (ist kein Muss und sofern passend) die im Footer genannte Partnerseite auflösen und evtl. in grau eine Auswahl im unteren Bereich der Startseite nennen.
Was ist Ihr erster Eindruck von der Startseite https://wegfinderei.de ? Was gefällt Ihnen nicht und würden Sie ändern wollen?

```html
<!DOCTYPE html>
<html lang="de">
<head>
<meta charset="utf-8">
<title>Wegfinderei – Einfach. Schöner. Verreisen.</title>
<link href="https://fonts.googleapis.com/css2?family=Roboto:wght@300;400;500;700;900&display=swap" rel="stylesheet">
<style>
:root{
  --teal:#1ec8b8;
  --navy:#1b1f4d;
  --ink:#2c3564;
  --muted:#5b6282;
  --grey-bg:#ececec;
  --green:#36b86a;
  --blue:#4a6fd4;
  --red:#cf1d1d;
  --purple:#b88fd7;
  --white:#fff;
}
*{box-sizing:border-box;margin:0;padding:0}
html,body{width:1200px;height:3891px;overflow:hidden}
body{font-family:'Roboto',sans-serif;color:var(--ink);background:#fff;position:relative}
.abs{position:absolute}
a{color:inherit;text-decoration:none}

/* hero */
.hero{position:absolute;left:0;top:0;width:1200px;height:632px;
  background:linear-gradient(180deg,#3b4a52 0%,#8a8a6c 22%,#c9a35a 32%,#6f7a52 45%,#3f5a34 70%,#2a3a24 100%);color:#fff;text-align:center}
.brand{position:absolute;top:24px;left:0;width:100%;font-size:20px;font-weight:400;letter-spacing:.5px}
.brand small{display:block;font-size:9px;opacity:.85;margin-top:2px;letter-spacing:.2px}
.main-nav{position:absolute;top:76px;left:137px;display:flex;gap:26px;font-size:12.5px;font-weight:700}
.main-nav a.active{color:var(--teal)}
.hero .kicker{position:absolute;top:188px;width:100%;font-size:21px;font-weight:400}
.hero h1{position:absolute;top:218px;width:100%;font-size:58px;font-weight:700;letter-spacing:-.5px}
.search{position:absolute;left:376px;top:304px;width:452px;height:42px;background:#fff;border-radius:21px;color:#777;font-size:15px;text-align:left;padding:12px 26px}
.search svg{position:absolute;right:18px;top:9px}
.hero-tabs{position:absolute;top:380px;left:0;width:100%;display:flex;justify-content:center;gap:26px;font-size:13.5px;font-weight:700}
.hero-tabs .active{color:var(--teal);border-bottom:2px solid var(--teal);padding-bottom:4px}
.hero p{position:absolute;top:420px;left:255px;width:690px;font-size:11.8px;line-height:19.6px;font-weight:500}

/* categories */
.cat-list{position:absolute;left:38px;top:695px;width:276px;height:560px;background:#fff;border-radius:8px;box-shadow:0 4px 18px rgba(0,0,0,.12);padding:34px 23px}
.cat-list h3{font-size:13px;font-weight:700;margin-bottom:10px}
.cat-list li{list-style:none;font-size:11px;line-height:22.4px;color:var(--muted)}
.pill-sm{display:inline-block;margin-top:14px;padding:7px 11px;border-radius:14px;background:#f0f0f0;font-size:8.5px;font-weight:700;letter-spacing:.3px}
.tile{position:absolute;border-radius:4px;overflow:hidden;color:#fff;font-size:17px;line-height:21px}
.tile span{position:absolute;left:20px;bottom:20px}
.dots{position:absolute;display:flex;gap:8px}
.dots i{width:12px;height:12px;border-radius:50%;background:#c9c9c9;display:block}
.dots i.on{width:18px;height:18px;margin-top:-3px}

/* offers */
.offers{position:absolute;left:0;top:1392px;width:1200px;height:719px;background:var(--grey-bg)}
.sec-title{position:absolute;width:100%;text-align:center;font-size:30px;font-weight:300;color:#333a55}
.offer-tabs{position:absolute;top:102px;left:0;width:100%;display:flex;justify-content:center;gap:26px;font-size:13.5px;font-weight:700}
.offer-tabs .active{color:var(--green);border-bottom:2px solid var(--green);padding-bottom:4px}
.card{position:absolute;top:151px;width:258px;height:458px;background:#fff;border-radius:6px;overflow:hidden;box-shadow:0 3px 10px rgba(0,0,0,.08)}
.card .ph{height:150px;border-bottom:5px solid var(--c)}
.card h4{color:var(--c);font-size:17.5px;font-weight:400;line-height:21px;margin:14px 19px 10px}
.card ul{margin:0 19px 0 32px;font-size:10.8px;line-height:15.8px;color:var(--muted)}
.card .price{margin:18px 19px 2px;font-size:19px;font-weight:700}
.card .note{margin:0 19px;font-size:10.5px;color:var(--muted)}
.card .btn{display:block;margin:17px 19px 0;height:41px;border-radius:21px;background:var(--c);color:#fff;text-align:center;line-height:41px;font-size:13px;font-weight:700;letter-spacing:.4px}
.card .more{display:block;width:104px;margin:14px auto 0;padding:6px 0;text-align:center;border-radius:12px;background:#f0f0f0;font-size:8.5px;font-weight:700;text-decoration:underline}

/* magazine */
.mag{position:absolute;overflow:hidden;color:#fff}
.mag h3{position:absolute;left:34px;font-size:31px;font-weight:400;line-height:36px}
.mag .read{position:absolute;left:34px;background:#fff;color:#222;font-size:9.5px;font-weight:700;padding:8px 20px;border-radius:15px}

/* quiz + newsletter */
.quiz-bg{position:absolute;left:0;top:2938px;width:655px;height:468px;background:var(--grey-bg)}
.quiz{position:absolute;left:56px;top:3027px;width:535px;height:336px;background:#fff;border-radius:4px;text-align:center}
.quiz h4{font-size:19.5px;font-weight:500;margin-top:24px}
.opt{position:absolute;width:143px;height:88px;background:#efefef;border-radius:6px;text-align:center;font-size:15px;font-weight:700;padding-top:14px}
.opt svg{display:block;margin:0 auto 6px}
.step{position:absolute;bottom:22px;width:100%;font-size:19.5px;font-weight:500}
.news{position:absolute;left:655px;top:2938px;width:545px;height:468px;background:var(--purple);color:#fff}
.news h3{position:absolute;left:75px;top:78px;width:410px;font-size:29px;line-height:35px;font-weight:900}
.news .field{position:absolute;left:51px;top:232px;width:274px;height:46px;background:#fff;border-radius:23px;color:#888;padding:14px 24px;font-size:15px}
.news .send{position:absolute;left:334px;top:232px;width:123px;height:46px;border-radius:23px;background:#3b2f6a;text-align:center;line-height:46px;font-size:13px;font-weight:700}
.news small{position:absolute;left:75px;top:300px;width:330px;font-size:7.6px;line-height:11.6px;opacity:.85}

/* footer */
footer{position:absolute;left:0;top:3406px;width:1200px;height:485px;background:var(--navy);color:#fff}
footer h5{position:absolute;left:56px;color:var(--teal);font-size:15px;font-weight:700}
.fcol{position:absolute;font-size:16px;line-height:29px}
.flogo{position:absolute;left:786px;top:70px;font-size:33px;font-weight:400;letter-spacing:.5px}
.ftag{position:absolute;left:790px;top:112px;font-size:15px;font-weight:500}
.ftext{position:absolute;left:790px;top:154px;width:350px;font-size:12.4px;line-height:22.6px}
.ftext + .ftext{top:310px}
.social{position:absolute;left:790px;top:404px;display:flex;gap:26px}
.social i{display:block;width:22px;height:22px;border:2px solid #8a8fb0;border-radius:50%}
.copy{position:absolute;left:56px;top:428px;font-size:11px;color:#b8bcd6}
</style>
</head>
<body>

<header class="hero">
  <div role="img" aria-label="Hügellandschaft im Abendlicht mit Sonnenuntergang und Wolken" class="abs" style="inset:0;background:radial-gradient(ellipse at 68% 28%,rgba(255,210,120,.7),rgba(255,200,100,0) 35%)"></div>
  <div class="brand">WEGFINDEREI<small>Jeder Weg ein neues Ziel</small></div>
  <nav class="main-nav">
    <a class="active">Reiseangebote</a><a>Aktivitäten&amp;Touren</a><a>Hotels</a><a>Flüge</a><a>Konzerte&amp;Events</a><a>Reisemagazin</a><a>Dein Freebie</a><a>Kurzurlaube&amp;Hotelarrangements</a>
  </nav>
  <div class="kicker">Topaktuelle Reiseangebote für 2021/2022</div>
  <h1>Einfach. Schöner. Verreisen.</h1>
  <div class="search">Reiserubrik, Reiseland, Stadt oder Stichwort
    <svg width="26" height="26" viewBox="0 0 26 26" fill="none" stroke="#111" stroke-width="2.2"><circle cx="11" cy="11" r="8"/><path d="M17 17l7 7"/></svg>
  </div>
  <div class="hero-tabs"><span class="active">Reiseangebote</span><span>Aktivitäten&amp;Touren</span><span>Hotels</span><span>Flüge</span><span>Konzerte&amp;Events</span></div>
  <p>Frische Urlaubsideen und Reiseangebote namhafter (Spezial-) Reiseveranstalter aus über 50 Themengebieten – genau das Richtige für all diejenigen, die qualitativ hochwertige Reiseangebote lieben, eine große Vielfalt bei der Reiseplanung schätzen und unkompliziert per Klick zur Buchungsmöglichkeit kommen wollen. Der Clou dabei? Such' Dir Deinen Urlaub z.B. nach Deinem Hobby aus oder lass' Dich durch die vielfältigen Filterfunktionen von nächsten Kurzurlaub, Kulturreisen oder Singlereise begeistern. Beste Urlaubslaune und charmante Urlaubsmomente versprechen auch Reisegutscheine für Kurzreisen und Online Tickets für Aktivitäten!</p>
</header>

<section class="categories">
  <aside class="cat-list">
    <h3>Kategorien:</h3>
    <ul>
      <li>Autoreisen und Autorundreisen (76)</li><li>Badeurlaub &amp; Strandurlaub (111)</li><li>Bahnreisen (82)</li><li>Best of Reisen (42)</li><li>Busreisen (60)</li><li>Camping und Mobilehomes (137)</li><li>Cluburlaub (40)</li><li>Erlebnisreisen (960)</li><li>Expeditionen (12)</li><li>Fahrradreisen (111)</li><li>Familienreisen (84)</li><li>Ferienhäuser und Ferienwohn. (12707)</li><li>Flußkreutzfahrten (493)</li><li>Frauenreisen</li><li>Freizeitparks und Zoos (62)</li><li>Golfreisen (3)</li><li>Gourmetreisen (38)</li><li>Haubootreisen (25)</li><li>Kinder- und Jugenreisen</li>
    </ul>
    <span class="pill-sm">MEHR RUBRIKEN</span>
  </aside>
  <div class="tile" role="img" aria-label="Kurvige Straße durch herbstlichen Wald" style="left:333px;top:677px;width:442px;height:308px;background:linear-gradient(160deg,#d9762a,#a84d1e 55%,#4a4a48)"><span>Autorundreisen und<br>Autoreisen (76)</span></div>
  <div class="tile" role="img" aria-label="Reisende im Zugabteil" style="left:779px;top:677px;width:365px;height:241px;background:linear-gradient(160deg,#9aa8a6,#55646a 60%,#2d3540)"><span>Bahnreisen (82)</span></div>
  <div class="tile" role="img" aria-label="Wohnmobil im Wald" style="left:779px;top:923px;width:365px;height:174px;background:linear-gradient(160deg,#6d5a3a,#8c8a78 50%,#3d4a30)"><span>Camping und Mobilehomes (137)</span></div>
  <div class="tile" role="img" aria-label="Hängematte am Strand" style="left:333px;top:990px;width:442px;height:286px;background:linear-gradient(160deg,#6fc6e0,#3a9ac0 45%,#c9b79a 80%)"><span>Badeurlaub &amp;<br>Strandurlaub (111)</span></div>
  <div class="tile" role="img" aria-label="Wanderweg im grünen Wald" style="left:779px;top:1102px;width:365px;height:174px;background:linear-gradient(160deg,#5f8a4a,#2f5228 60%,#1f3a1c)"><span>Erlebnisreisen (960)</span></div>
  <div class="dots" style="left:717px;top:1306px"><i class="on" style="background:var(--teal)"></i><i></i><i></i><i></i><i></i><i></i></div>
</section>

<section class="offers">
  <h2 class="sec-title" style="top:38px">Unsere Top-Angebote für Sie</h2>
  <div class="offer-tabs"><span class="active">Wellness im Herbst</span><span>Kurzurlaube &amp; Hotelarrangements</span><span>Reiseangebote des Monats</span></div>

  <article class="card" style="left:56px;--c:var(--green)">
    <div class="ph" role="img" aria-label="Ostseestrand mit Hotel" style="background:linear-gradient(180deg,#6ea8d8,#3d7fb8 45%,#d8cdb0 80%)"></div>
    <h4>Wellnesshotel mit Goldbad &amp; Massage - Ostsee</h4>
    <ul><li>5 Übernachtungen im Standard-DZ</li><li>Begrüßungsdrink</li><li>Reichhaltiges Frühstücksbuffet</li><li>Abends vielseitiges kalt-warmes Bu...</li><li>Klassische Teilmassage (20min.)</li></ul>
    <div class="price">ab € 229,00</div><div class="note">5 Übernachtungen inkl.Halbpension *</div>
    <a class="btn">WEITER ZUM ANGEBOT</a><a class="more">MEHR DETAILS</a>
  </article>
  <article class="card" style="left:333px;--c:var(--blue)">
    <div class="ph" role="img" aria-label="Dünengras an der Küste" style="background:linear-gradient(180deg,#c9d8dc,#8ea79a 50%,#6b7a5c)"></div>
    <h4>Wellness-Auszeit mit Meerblick - Kolberg</h4>
    <ul><li>5 Übernachtungen im Standard-DZ</li><li>Begrüßungsdrink</li><li>Reichhaltiges Frühstücksbuffet</li><li>Abends vielseitiges kalt-warmes Bu...</li><li>Entspannte Teilkörpermassage</li></ul>
    <div class="price">ab € 169,00</div><div class="note">3 Übernachtungen inkl. Frühstück *</div>
    <a class="btn">WEITER ZUM ANGEBOT</a><a class="more">MEHR DETAILS</a>
  </article>
  <article class="card" style="left:609px;--c:var(--red)">
    <div class="ph" role="img" aria-label="Kurpark mit Kolonnade" style="background:linear-gradient(180deg,#9ec0e0,#6f9a50 45%,#3e6a2a)"></div>
    <h4>Kompforthotel mit Spa-Bereich-Marienbad</h4>
    <ul><li>5 Übernachtungen im Standard-DZ</li><li>Begrüßungsdrink</li><li>Reichhaltiges Frühstücksbuffet</li><li>Abends vielseitiges kalt-warmes Bu...</li><li>Klassische Teilmassage (20min.)</li></ul>
    <div class="price">ab € 299,00</div><div class="note">5 Übernachtungen inkl. Halbpension *</div>
    <a class="btn">WEITER ZUM ANGEBOT</a><a class="more">MEHR DETAILS</a>
  </article>
  <article class="card" style="left:886px;--c:var(--red)">
    <div class="ph" role="img" aria-label="Frühstückstisch mit Obst" style="background:linear-gradient(160deg,#8a5a38,#c89a60 50%,#5a3a24)"></div>
    <h4>Wellnessreise in die Seenstadt Schwerin</h4>
    <ul><li>5 Übernachtungen im Standard-DZ</li><li>Begrüßungsdrink</li><li>Reichhaltiges Frühstücksbuffet</li><li>Abends vielseitiges kalt-warmes Bu...</li><li>Klassische Teilmassage (20min.)</li></ul>
    <div class="price">ab € 149,00</div><div class="note">2 Übernachtungen inkl. Frühstück *</div>
    <a class="btn">WEITER ZUM ANGEBOT</a><a class="more">MEHR DETAILS</a>
  </article>
  <div class="dots" style="left:543px;top:641px"><i class="on" style="background:var(--red)"></i><i></i><i></i><i></i><i></i><i></i></div>
</section>

<section class="magazine">
  <h2 class="sec-title" style="top:2152px">Unser Reisemagazin</h2>
  <article class="mag" role="img" aria-label="Reisereportage Kuba" style="left:56px;top:2217px;width:535px;height:659px;background:linear-gradient(160deg,#2f4fd8,#1f36a8 40%,#5a3e30 75%,#2a201c)">
    <h3 style="top:522px">Kuba - Kolonialromantik und<br>ein Hauch von Revolution</h3><span class="read" style="top:600px">ARTIKEL LESEN</span>
  </article>
  <article class="mag" role="img" aria-label="Speicherstadt in Hamburg" style="left:595px;top:2217px;width:549px;height:328px;background:linear-gradient(160deg,#c8b8a8,#8a4a38 45%,#4a2a24)">
    <h3 style="top:184px">Hamburg - Eine Reise mit<br>Fernwehgarantie</h3><span class="read" style="top:260px">ARTIKEL LESEN</span>
  </article>
  <article class="mag" role="img" aria-label="Stadtansicht von Helsinki am Hafen" style="left:595px;top:2550px;width:549px;height:326px;background:linear-gradient(180deg,#9cbde0,#dde4e8 45%,#6a7a84 70%,#3a4a58)">
    <h3 style="top:190px">Helsinki - Die weiße Stadt<br>am Meer</h3><span class="read" style="top:266px">ARTIKEL LESEN</span>
  </article>
</section>

<div class="quiz-bg"><h2 class="sec-title" style="top:42px;font-size:29px">Was für ein Reisetyp sind Sie?</h2></div>
<div class="quiz">
  <h4>Welches Verkehrsmittel bevorzugen Sie?</h4>
  <div class="opt" style="left:40px;top:63px"><svg width="34" height="40" viewBox="0 0 34 40" fill="none" stroke="#2c3564" stroke-width="2"><rect x="5" y="3" width="24" height="28" rx="4"/><path d="M5 17h24M10 25h2M22 25h2M9 31l-4 7M25 31l4 7"/></svg>ZUG</div>
  <div class="opt" style="left:195px;top:63px"><svg width="60" height="34" viewBox="0 0 60 34" fill="none" stroke="#2c3564" stroke-width="2"><path d="M4 24v-7l8-3 7-8h20l9 8 8 3v7z" fill="#e24a4a"/><circle cx="16" cy="25" r="5" fill="#fff"/><circle cx="44" cy="25" r="5" fill="#fff"/></svg>AUTO</div>
  <div class="opt" style="left:350px;top:63px"><svg width="40" height="40" viewBox="0 0 40 40" fill="none" stroke="#2c3564" stroke-width="2"><rect x="6" y="3" width="28" height="30" rx="3" fill="#f5b82a"/><path d="M6 18h28M12 27h3M25 27h3M10 33v4M30 33v4"/></svg>BUS</div>
  <div class="opt" style="left:118px;top:171px"><svg width="50" height="40" viewBox="0 0 50 40" fill="#f08a1c"><path d="M6 22l14-2 12-14c3-3 7-2 5 2L27 22l10 12-4 2-12-10-12 3z"/></svg>FLUGZEUG</div>
  <div class="opt" style="left:273px;top:171px"><svg width="64" height="40" viewBox="0 0 64 40" fill="none" stroke="#2f8a48" stroke-width="2.4"><circle cx="14" cy="26" r="10"/><circle cx="50" cy="26" r="10"/><path d="M14 26l10-16h16l10 16M24 10l8 16 8-16M22 7h6"/></svg>FAHRRAD</div>
  <div class="step">Schritt 1 von 4</div>
</div>

<section class="news">
  <div role="img" aria-label="Angedeuteter Globus als Hintergrundmotiv" class="abs" style="left:40px;top:-20px;width:480px;height:480px;border-radius:50%;background:radial-gradient(circle,rgba(255,255,255,.12),rgba(255,255,255,0) 70%)"></div>
  <h3>Exklusive Angebote, Reise-Deals, Gutschein-Aktionen und bis zu 70 % Preisvorteil.</h3>
  <div class="field">Ihre E-Mail Adresse</div><div class="send">SENDEN</div>
  <small>Ich willige ein, den Wegfinderei-Newsletter zu erhalten und dass meine personenbezogenen Daten (E-Mail-Adresse) zum Zwecke der Werbung zum Thema Reisen sowie reisenahe Produkte und Dienstleistungen gespeichert und verarbeitet werden.</small>
</section>

<footer>
  <h5 style="top:72px">Rubriken</h5>
  <div class="fcol" style="left:56px;top:98px">Reiseangebote<br>Aktivitäten &amp; Touren<br>Flüge</div>
  <div class="fcol" style="left:256px;top:98px">Konzerte&amp;Events<br>Reisemagazin<br>Dein Freebie</div>
  <div class="fcol" style="left:472px;top:98px">Kurzurlaube &amp;<br>Hotelarrangements</div>
  <h5 style="top:240px">Service</h5>
  <div class="fcol" style="left:56px;top:266px">Kontakt<br>Partnerprogramm<br>Partner<br>Social Media</div>
  <div class="fcol" style="left:256px;top:266px">Impressum<br>Datenschutzerklärung<br>Nutzungsbedingungen<br>FAQs</div>
  <div class="fcol" style="left:472px;top:266px">Reisezitate<br>Visum beantragen</div>
  <div class="flogo">WEGFINDEREI</div>
  <div class="ftag">Jeder Weg ein neues Ziel</div>
  <p class="ftext">Bei der auf dieser Seite dargestellten Reise- und Ticket-angebote, handelt es sich um Angebote von dritten Unter-nehmen, auf die WEGFINDEREI keinen Einfluss hat.</p>
  <p class="ftext" style="top:230px">Die mit Sternchen (*) gekennzeichneten Links sind Provisions-Links, auch Affiliate-Links genannt. Wenn Sie auf einen solchen Link klicken und auf der Zielseite etwas kaufen, bekommen wir vom betreffenden Anbieter eine Vermittlerprovision. Es entstehen für Sie keine Nachteile beim Kauf oder Preis.</p>
  <div class="social"><i aria-label="Social-Media-Kanal 1"></i><i aria-label="Social-Media-Kanal 2"></i><i aria-label="Social-Media-Kanal 3"></i><i aria-label="Social-Media-Kanal 4"></i></div>
  <div class="copy">© Copyright 2021 wegfinderei.de</div>
</footer>

</body>
</html>
```